Innovative Media Company needs Web Design

We need a web design for a new multimedia product that we are launching to potential partners and investors. The initial website we are looking to launch consists of three pages:
1.) A home/feature set page
2.) An account landing page
3.) An about us page
We would like the style of our website to be VERY similar to the following site: http://www.brintaro.com/tundra.
We have worked a bit on this project with a previous designer but were not happy with the results. As a guideline, you may refer to their previous work and the Tundra 88 website.
We realize this prize is a bit low for this project. However, there is a great opportunity for follow-on work. We are hoping to make a long-term business relationship with a high quality web-developer.
Attached are the product logo and our previous designer's work. Please let me know if you have any questions.
Thank you.
All,
Thanks for your submissions. Please note that rather than have headers that state "Enhanced TV Functionality" and "Seamless Device Integration", I would like to see all features (the six or seven boxes) in the same section. Also, please revise your designs to have the following statement below the picture that stretches across the screen and above the feature descriptions:
"Available via apps for the television and mobile devices,
naLix technology integrates numerous media components to provide users with
enhanced TV functionality and seamless device integration for an unparalleled
personalized viewing experience."
Thanks you.

```html
<!DOCTYPE html>
<html lang="en">
<head>
<meta charset="utf-8">
<title>naLix – Next Generation Television</title>
<link rel="stylesheet" href="https://fonts.googleapis.com/css2?family=Signika:wght@300;400&family=PT+Sans:wght@400;700&display=swap">
<style>
  :root {
    --header-bg: #ececec;
    --header-top: #f6f6f6;
    --ink: #3a3a3a;
    --ink-soft: #555;
    --nav-divider: #c8c8c8;
    --hero-bg: #1e1e1e;
    --hero-bg-light: #2c2c2c;
    --hero-text: #f2f2f2;
    --button-bg: #e6e6e6;
    --page-bg: #ffffff;
    --rule: #9a9a9a;
    --col-divider: #e2e2e2;
    --footer-bg: #2a2a2a;
    --footer-bg-dark: #1c1c1c;
    --footer-text: #d8d8d8;
    --footer-line: #3c3c3c;
    --footer-mark: #5a5a5a;
  }
  * { margin: 0; padding: 0; box-sizing: border-box; }
  html, body { width: 683px; height: 1200px; overflow: hidden; background: var(--page-bg); }
  body { position: relative; font-family: "PT Sans", sans-serif; color: var(--ink); }
  .display { font-family: "Signika", sans-serif; font-weight: 300; }
  .abs { position: absolute; }

  /* Header */
  .site-header { left: 0; top: 0; width: 683px; height: 84px;
    background: linear-gradient(var(--header-top), var(--header-bg)); border-top: 3px solid #d4d4d4; }
  .brand { left: 26px; top: 28px; display: flex; align-items: center; gap: 8px; }
  .brand-dot { width: 22px; height: 22px; border-radius: 50%; background: var(--ink); }
  .brand-name { font-family: "Signika", sans-serif; font-weight: 400; font-size: 34px; color: var(--ink); line-height: 1; }
  .main-nav { right: 52px; top: 44px; display: flex; font-family: "Signika", sans-serif; font-weight: 300; font-size: 11.5px; color: var(--ink); }
  .main-nav a { color: inherit; text-decoration: none; padding: 1px 14px; border-left: 1px solid var(--nav-divider); }
  .main-nav a:first-child { border-left: none; }

  /* Hero */
  .hero { left: 0; top: 84px; width: 683px; height: 302px;
    background: radial-gradient(ellipse at 35% 45%, var(--hero-bg-light), var(--hero-bg) 70%); }
  .hero-media { left: 50px; top: 44px; width: 296px; height: 212px; border-radius: 3px;
    background: linear-gradient(135deg, #4e5a3a 0%, #c8d2c0 40%, #3e4a2c 70%, #2a3020 100%);
    border: 10px solid #0d0d0d; }
  .hero-copy { left: 422px; top: 82px; color: var(--hero-text); }
  .hero-copy .lead { font-size: 21px; line-height: 1.1; }
  .hero-copy .big { font-size: 31px; line-height: 1.05; }
  .learn-more { left: 426px; top: 176px; width: 77px; height: 23px; border-radius: 3px;
    background: var(--button-bg); color: var(--ink); font-size: 12px; line-height: 23px; text-align: center; }
  .hero-arrows { left: 614px; top: 266px; }

  /* Intro */
  .intro-title { left: 20px; top: 406px; font-size: 24px; color: var(--ink); }
  .intro-text { left: 20px; top: 444px; width: 636px; font-size: 7.6px; line-height: 11.6px; color: var(--ink-soft); }
  .rule { left: 75px; width: 533px; border-top: 1px dotted var(--rule); }

  /* Features */
  .feature { width: 200px; }
  .feature h3 { font-family: "Signika", sans-serif; font-weight: 300; font-size: 17px; color: var(--ink); height: 24px; }
  .feature .media { margin-top: 4px; height: 108px; border-radius: 3px; }
  .feature p { margin-top: 16px; font-size: 7.9px; line-height: 11.8px; color: var(--ink-soft); width: 200px; }
  .feature .more { margin-top: 10px; font-size: 9.5px; color: var(--ink-soft); letter-spacing: .2px; }
  .media-tv { width: 160px; background: linear-gradient(#6e9bd0 0%, #b8d0e8 45%, #d84a2a 60%, #e8b030 80%, #3a6a2a 100%); border: 4px solid #111; }
  .media-tablet { width: 138px; background: linear-gradient(#e8ecf2, #b8c2d0); border: 6px solid #1a1a1a; }
  .media-slate { width: 170px; margin-left: 4px; background: linear-gradient(160deg, #f4f4f4 0%, #1e3a8a 45%, #2a2a2a 75%, #f4f4f4 100%); }
  .col-divider { width: 1px; background: var(--col-divider); }

  /* Footer */
  .site-footer { left: 0; top: 1009px; width: 683px; height: 191px;
    background: linear-gradient(var(--footer-bg), var(--footer-bg-dark)); color: var(--footer-text); }
  .quick-title { left: 25px; top: 16px; font-size: 16px; color: var(--footer-text); }
  .quick-col { top: 44px; font-size: 8px; }
  .quick-col li { list-style: none; height: 18.6px; line-height: 18px; border-bottom: 1px solid var(--footer-line); }
  .quick-col li:last-child { border-bottom: none; }
  .footer-mark { left: 528px; top: 72px; font-family: "Signika", sans-serif; font-weight: 400; font-size: 30px; color: var(--footer-mark); }
  .footer-bar { left: 0; top: 164px; width: 683px; height: 27px; border-top: 1px solid var(--footer-line);
    font-size: 7.5px; line-height: 26px; padding-left: 19px; color: var(--footer-text); }
</style>
</head>
<body>

<header class="site-header abs">
  <div class="brand abs"><span class="brand-dot"></span><span class="brand-name">naLix</span></div>
  <nav class="main-nav abs"><a href="#">Home</a><a href="#">Account Page</a><a href="#">About Us</a></nav>
</header>

<section class="hero abs">
  <div class="hero-media abs" role="img" aria-label="Flat-screen television showing a sunlit forest scene"></div>
  <div class="hero-copy abs display">
    <div class="lead">Step into the</div>
    <div class="big">Next Generation</div>
    <div class="big">of television</div>
  </div>
  <div class="learn-more abs display">learn more &rsaquo;</div>
  <svg class="hero-arrows abs" width="30" height="20" viewBox="0 0 30 20">
    <path d="M8 2 L2 10 L8 18" fill="none" stroke="#cfcfcf" stroke-width="1.2"/>
    <path d="M22 2 L28 10 L22 18" fill="none" stroke="#cfcfcf" stroke-width="1.2"/>
  </svg>
</section>

<h1 class="intro-title abs display">Get the next generation television now !</h1>
<p class="intro-text abs">E-Commerce is a major progress in technology that has changed the way in which the customers now purchase information, products and the services. It's the new way of providing an opportunity to make your products and services avaailable in the global market 24 hours a day through Internet&nbsp; Brightwave Studio is specialized in handling advanced web projects and the ongoing projects that require permanent maintenance and support .We like challenges and do complete these challenge with expertise we like solving questions that arises in such projects as these helps us to grow also.</p>

<div class="rule abs" style="top:510px"></div>

<!-- Feature row one -->
<div class="col-divider abs" style="left:229px;top:532px;height:200px"></div>
<div class="col-divider abs" style="left:455px;top:532px;height:200px"></div>

<article class="feature abs" style="left:21px;top:527px">
  <h3>TV Functionality</h3>
  <div class="media media-tv" role="img" aria-label="Television showing a tulip field with a windmill"></div>
  <p>Brightwave Studio is specialized in handling advanced web projects and the ongoing projects that require permanent maintenance and support .We like challenges and do complete these challenge with expertise</p>
  <div class="more">READ MORE &rsaquo;</div>
</article>
<article class="feature abs" style="left:245px;top:527px">
  <h3>Device Integration</h3>
  <div class="media media-tablet" role="img" aria-label="Tablet and two smartphones showing a media app"></div>
  <p>Brightwave Studio is specialized in handling advanced web projects and the ongoing projects that require permanent maintenance and support .We like challenges and do complete these challenge with expertise</p>
  <div class="more">READ MORE &rsaquo;</div>
</article>
<article class="feature abs" style="left:474px;top:527px">
  <h3>Next Level product</h3>
  <div class="media media-slate" role="img" aria-label="Slate tablet with stylus"></div>
  <p>Brightwave Studio is specialized in handling advanced web projects and the ongoing projects that require permanent maintenance and support .We like challenges and do complete these challenge with expertise</p>
  <div class="more">READ MORE &rsaquo;</div>
</article>

<div class="rule abs" style="top:762px"></div>

<!-- Feature row two -->
<div class="col-divider abs" style="left:229px;top:783px;height:200px"></div>
<div class="col-divider abs" style="left:455px;top:783px;height:200px"></div>

<article class="feature abs" style="left:21px;top:778px">
  <h3>TV Functionality</h3>
  <div class="media media-tv" role="img" aria-label="Television showing a tulip field with a windmill"></div>
  <p>Brightwave Studio is specialized in handling advanced web projects and the ongoing projects that require permanent maintenance and support .We like challenges and do complete these challenge with expertise</p>
  <div class="more">READ MORE &rsaquo;</div>
</article>
<article class="feature abs" style="left:245px;top:778px">
  <h3>Device Integration</h3>
  <div class="media media-tablet" role="img" aria-label="Tablet and two smartphones showing a media app"></div>
  <p>Brightwave Studio is specialized in handling advanced web projects and the ongoing projects that require permanent maintenance and support .We like challenges and do complete these challenge with expertise</p>
  <div class="more">READ MORE &rsaquo;</div>
</article>
<article class="feature abs" style="left:474px;top:778px">
  <h3>Next Level product</h3>
  <div class="media media-slate" role="img" aria-label="Slate tablet with stylus"></div>
  <p>Brightwave Studio is specialized in handling advanced web projects and the ongoing projects that require permanent maintenance and support .We like challenges and do complete these challenge with expertise</p>
  <div class="more">READ MORE &rsaquo;</div>
</article>

<footer class="site-footer abs">
  <h2 class="quick-title abs display">Quick links</h2>
  <ul class="quick-col abs" style="left:25px;width:90px">
    <li>Home Page</li><li>About Our Company</li><li>Services Overview</li><li>Product List</li><li>Testimonials</li>
  </ul>
  <ul class="quick-col abs" style="left:120px;width:80px">
    <li>Recent Blog</li><li>Next Generation</li><li>Television</li><li>News &amp; Blog</li><li>FAQ</li>
  </ul>
  <ul class="quick-col abs" style="left:204px;width:86px">
    <li>Product Goes here</li><li>IInd Product</li><li>IIIrd Product</li><li>More Products</li>
  </ul>
  <ul class="quick-col abs" style="left:292px;width:96px">
    <li>Product Goes here</li><li>IInd Product</li><li>IIIrd Product</li><li>More Products</li>
  </ul>
  <ul class="quick-col abs" style="left:392px;width:64px">
    <li>Product Goes here</li><li>IInd Product</li><li>IIIrd Product</li><li>More Products</li>
  </ul>
  <div class="footer-mark abs">naLix</div>
  <div class="footer-bar abs">&copy; 2012 Company Name &nbsp;|&nbsp; All right reserved</div>
</footer>

</body>
</html>
```